Store Front Window Design

We have a beautiful corner store front dental practice with no window signage. Crazy I know...that's why we need your help.

The final design will be done in all vinyl unless unless you suggest a different medium (meaning we are open to some design idea like using frosted glass, etc...).

The windows provide a lot of natural light so the design needs to keep a lot of natural light coming into the office. Keep in mind vinyl is not opaque so keep the signage aesthetically pleasing and a minimalist design to allow as much natural light in as possible. The design should follow the aesthetic from our logo. or tie into at least. We want a cohesive brand aesthetic.

I submitted some general layout ideas. There is a blue banner with advertising words which we want to be used in the final version. Even though the lettering is black, in reality the letters will be a white vinyl on the outside of the window. When you submit your work, be sure to add any special instructions (aka tell me the vision for the letters is white not black, maybe gold leaf, or forested glass...stuff like that). AND YOU DO NOT HAVE TO FOLLOW MY PATTERN! YOU ARE ARTISTS AND WE ARE LOOKING FOR AN ARTISTIC EYE CATCHING PRESENTATION OF THIS INFORMATION. MAKE IT FLASHY AND ADD SOME AESTHETIC FROM THE TOOTH LOGO.

The store front is 6 windows roughly 60'' x 36'' The smaller windows below are 27'' x 36''. Around the corner there are 3 windows. they are 60'' x 27'' lower windows are 27" x 27". We would like to keep the bottom windows clear and keep the signage on the top windows, however, we are flexible.

The front 6 windows need to have this information worked into the design.

Practice name: Varden and Pellosi Dental & Orthodontics.
Phone numbers: Rosalind Varden DDS: 415.555.0187
Oskar Pellosi DDS:415.555.0243

Expertise: Dr. Varden General Dentistry & Orthodontics
Dr. Pellosi Oral Surgery & Sedation

Address: 1938 Birchwood Ave

A banner across the bottom of the top windows with some key advertisement words: "Clearmold" "Braces" "Implants" "Whiting" "Call today" "Free Consultation" "Oral Surgery" "Sedation". We like the two color idea. Its up to you to decide on the color combo. I used a Dark and light blue, but maybe a Blue and grey would nice to tire in the logo colors?

I have made some mock ideas to get the ball rolling but you do not have to stick to these designs at all, just as long as all the required information is there. Be creative with the layouts, fonts, color scheme, (just remember these are going on windows not necessarily a white background), and graphics/artistic flare (refer to logo for layout inspiration and use the logo as an actual graphic). We are running a miltimillion dollar dental practice so we want these windows to be eye catching to pull in patients and look like a million dollar design. Also all 6 windows dont need ot be used. I am really looking for creative design marketing.

The corner 3 windows need the following information: name, expertise, phone number, banner.

Dr. Varden, General Dentistry & Orthodontics, 415.555.0187
Dr. Pellosi, Oral Surgery & Sedation, 415.555.0243

There is also a front door that needs to be designed. The door is 60'' x 36'' (standard door size) We want simple white vinyl on the outside of the door. We need you to organize the information on the door, pick a easy to read font, maybe use the logo and use some of the front window signage aesthetic? Its up to you...but we we were initially thinking of just making the litters white and keep it simple but again you are the designers.

Practice name: Varden and Pellosi General Dentistry & Orthodontics

Address: 1938 Birchwood Ave

Phone numbers: Dr. Varden 415.555.0187
Dr. Pellosi 415.555.0243

Hours of operation: Mon: call for an appointment
Tues-Thurs: 9am-5pm
Sat: call for an appointment
Sun: Closed

A line saying we speak Spanish: Se Habla Espanol

*****************************************************************************************************
here are some design that we liked and some rough sketches I made to start the ball rolling. Keep in mind that there are 9 windows for the front because its a corner office, but not all of them have to have stuff on it. We want simple, streamline, classy high commanding price point aesthetic. I am hiring you for your artistic minds.

Target Market(s)

anyone who has dental needs

Industry/Entity Type

Dental

Font styles to use
Serif
Sans Serif

Colors

Designer to choose colors to be used in the design.

Requirements
Must have
• 1. The required information (see project description)
• 2. Logo
• 3. Advertisement banner running along the bottom of all 9 windows (6 in front and 3 on the side)
• NOTE: Look at pictures of the store to get a sense of the customers point of view and also as a reference to how your design will be broken up across several windows or maybe you design something special for every window. But we want the banner to run along all the windows to lead customs to the door on the side. Finally the letters will be done in white vinyl unless state otherwise, remember the window needs to let in natural light so the entire window can not be covered in vinyl.
Nice to have
• artistic flare yet simple and sleep and expensive looking aesthetic. work logo into the design.
Should not have
• The goal is to catch someone eye and give them important information about the practice.
• It should not just be words.
• It should not have to many words
• It must be readable font for cards driving by.

```html
<!DOCTYPE html>
<html lang="en">
<head>
<meta charset="utf-8">
<title>Varden and Pellosi Dental &amp; Orthodontics — Window Signage</title>
<link rel="stylesheet" href="https://fonts.googleapis.com/css2?family=Bebas+Neue&family=Oswald:wght@300;400&family=Mulish:wght@400;500&family=Pinyon+Script&display=swap">
<style>
  :root {
    --blue: #1b78d0;
    --blue-deep: #1565b5;
    --grey: #8d8e92;
    --grey-dark: #6b6c70;
    --text-grey: #555659;
    --stage: #e4e4e4;
    --white: #ffffff;
  }
  * { box-sizing: border-box; margin: 0; padding: 0; }
  html, body { width: 1064px; height: 1200px; overflow: hidden; }
  body { background: var(--stage); position: relative; font-family: "Mulish", sans-serif; }

  .panel { position: absolute; overflow: hidden; background: var(--white);
           box-shadow: 0 14px 18px -8px rgba(0,0,0,.35); }
  .panel > svg.shape { position: absolute; inset: 0; width: 100%; height: 100%; }
  .c { position: absolute; transform: translate(-50%, -50%); text-align: center; white-space: nowrap; }

  .label { position: absolute; transform: translateX(-50%); font-family: "Mulish", sans-serif;
           font-size: 22px; letter-spacing: .5px; color: #111; }

  .brand-mark { border: 3px solid var(--blue); border-radius: 50%; }
  .brand-name { font-family: "Mulish", sans-serif; font-weight: 500; color: var(--grey-dark); line-height: 1.15; }
  .brand-name span { display: block; }

  .display { font-family: "Bebas Neue", sans-serif; color: var(--blue-deep); line-height: 1; }
  .doc-name, .phone { font-family: "Oswald", sans-serif; font-weight: 300; color: var(--blue-deep); line-height: 1; }
  .doc-role { font-family: "Mulish", sans-serif; color: var(--text-grey); line-height: 1.3; }

  .banner { position: absolute; left: 0; background: var(--blue); }
  .banner::before, .banner::after { content: ""; position: absolute; left: 0; right: 0;
           border-top: 1px dashed rgba(255,255,255,.7); }
  .banner::before { top: 3px; } .banner::after { bottom: 3px; }
  .banner-item { position: absolute; top: 50%; transform: translate(-50%, -50%); color: var(--white);
           font-family: "Mulish", sans-serif; white-space: nowrap; }

  .icon-slot { position: absolute; transform: translate(-50%, -50%); background: var(--blue); border-radius: 6px; opacity: .9; }

  /* front door */
  .door { left: 23px; top: 38px; width: 364px; height: 606px; }
  .door .street-band { position: absolute; left: 0; top: 217px; width: 100%; height: 28px; background: var(--blue);
           color: var(--white); font-family: "Mulish", sans-serif; font-size: 21px; font-weight: 500;
           text-align: center; line-height: 28px; }
  .hours-box { position: absolute; left: 63px; top: 285px; width: 237px; height: 127px; border: 1px solid #b9b9b9; }
  .hours-title { position: absolute; left: 73px; top: 271px; width: 220px; height: 32px; background: var(--grey-dark);
           color: var(--white); font-family: "Bebas Neue", sans-serif; font-size: 29px; text-align: center; line-height: 34px; }
  .hours-line { font-size: 13.5px; color: var(--blue-deep); }
  .door-rule { position: absolute; left: 0; top: 559px; width: 100%; height: 3px; background: var(--blue); }
  .spanish { font-family: "Pinyon Script", cursive; font-size: 25px; color: #222; }

  /* corner windows */
  .corner { left: 473px; top: 38px; width: 565px; height: 606px; }
  .emblem-slot { position: absolute; left: 0; top: 234px; width: 183px; height: 184px;
           background: linear-gradient(180deg, var(--blue) 0%, var(--blue-deep) 100%); opacity: .85;
           border-radius: 0 40% 40% 0; }

  /* front windows */
  .front { left: 23px; top: 716px; width: 1017px; height: 410px; background: var(--grey); }
</style>
</head>
<body>

<!-- FRONT DOOR -->
<section class="panel door" aria-label="Front door signage">
  <svg class="shape" viewBox="0 0 364 606" preserveAspectRatio="none" aria-hidden="true">
    <path d="M230 0 C 300 20, 350 80, 364 140 L364 0 Z" fill="var(--blue)"/>
  </svg>
  <div class="c brand-mark" style="left:182px;top:60px;width:58px;height:58px;"></div>
  <div class="c brand-name" style="left:182px;top:126px;font-size:14px;letter-spacing:.6px;">
    <span>VARDEN AND PELLOSI</span><span>DENTAL &amp; ORTHODONTICS</span>
  </div>
  <div class="c display" style="left:182px;top:192px;font-size:60px;">1938</div>
  <div class="street-band">BIRCHWOOD AVENUE</div>

  <div class="hours-box"></div>
  <div class="hours-title">HOURS OF OPERATION</div>
  <div class="c hours-line" style="left:182px;top:322px;">Mon : Call for an appointment</div>
  <div class="c hours-line" style="left:182px;top:345px;">Tues - Thurs : 9am-5pm</div>
  <div class="c hours-line" style="left:182px;top:368px;">Sat : Call for an appointment</div>
  <div class="c hours-line" style="left:182px;top:390px;">Sun : Closed</div>

  <div class="c doc-name" style="left:95px;top:452px;font-size:23px;">DR. VARDEN</div>
  <div class="c doc-role" style="left:95px;top:490px;font-size:11px;">General Dentistry<br>&amp;<br>Orthodontics</div>
  <div class="c phone" style="left:95px;top:530px;font-size:24px;">415.555.0187</div>

  <div class="c doc-name" style="left:270px;top:452px;font-size:23px;">DR. PELLOSI</div>
  <div class="c doc-role" style="left:270px;top:490px;font-size:11px;">Oral Surgery<br>&amp;<br>Sedationeral Dentistry</div>
  <div class="c phone" style="left:270px;top:530px;font-size:24px;">415.555.0243</div>

  <div class="door-rule"></div>
  <div class="c spanish" style="left:182px;top:585px;">Se Habla Espanol</div>
</section>
<div class="label" style="left:205px;top:664px;">FRONT DOOR</div>

<!-- CORNER 3 WINDOWS -->
<section class="panel corner" aria-label="Corner three window signage">
  <svg class="shape" viewBox="0 0 565 606" preserveAspectRatio="none" aria-hidden="true">
    <rect x="0" y="0" width="565" height="310" fill="var(--blue)"/>
    <rect x="0" y="310" width="565" height="296" fill="var(--grey)"/>
    <ellipse cx="282" cy="310" rx="337" ry="322" fill="var(--white)"/>
  </svg>
  <div class="c brand-mark" style="left:282px;top:44px;width:46px;height:46px;"></div>
  <div class="c brand-name" style="left:282px;top:91px;font-size:11.5px;letter-spacing:.5px;">
    <span>VARDEN AND PELLOSI</span><span>DENTAL &amp; ORTHODONTICS</span>
  </div>
  <div class="c display" style="left:304px;top:160px;font-size:52px;word-spacing:10px;">1938 BIRCHWOOD AVENUE</div>
  <svg style="position:absolute;left:71px;top:189px;" width="468" height="6" aria-hidden="true">
    <line x1="0" y1="1" x2="468" y2="1" stroke="var(--blue)" stroke-width="1.5"/>
    <line x1="0" y1="5" x2="468" y2="5" stroke="var(--blue)" stroke-width="1"/>
  </svg>

  <div class="emblem-slot" role="img" aria-label="Winged staff medical emblem in blue"></div>

  <div class="c doc-name" style="left:282px;top:246px;font-size:29px;">DR. VARDEN</div>
  <div class="c doc-role" style="left:282px;top:297px;font-size:14px;line-height:1.28;">General Dentistry<br>&amp;<br>Orthodontics</div>
  <div class="c phone" style="left:282px;top:347px;font-size:32px;">415.555.0187</div>

  <div class="c doc-name" style="left:469px;top:246px;font-size:29px;">DR. PELLOSI</div>
  <div class="c doc-role" style="left:469px;top:297px;font-size:14px;line-height:1.28;">Oral Surgery<br>&amp;<br>Sedationeral Dentistry</div>
  <div class="c phone" style="left:469px;top:347px;font-size:32px;">415.555.0243</div>

  <div class="banner" style="top:420px;width:100%;height:32px;">
    <div class="banner-item" style="left:93px;font-size:13px;">ACCEPTING NEW PATIENCE</div>
    <div class="banner-item" style="left:282px;font-size:13px;">CALL TODAY</div>
    <div class="banner-item" style="left:470px;font-size:13px;">FREE CONSULTATION</div>
  </div>

  <div class="icon-slot" role="img" aria-label="Icon of a patient in the dental chair" style="left:92px;top:509px;width:56px;height:54px;"></div>
  <svg class="c" style="left:282px;top:509px;" width="58" height="58" viewBox="0 0 24 24" aria-hidden="true">
    <path fill="var(--blue)" d="M6.6 10.8c1.4 2.8 3.8 5.1 6.6 6.6l2.2-2.2c.3-.3.7-.4 1-.2 1.1.4 2.3.6 3.6.6.6 0 1 .4 1 1V20c0 .6-.4 1-1 1C10.6 21 3 13.4 3 4c0-.6.4-1 1-1h3.5c.6 0 1 .4 1 1 0 1.3.2 2.5.6 3.6.1.3 0 .7-.2 1L6.6 10.8z"/>
    <path fill="none" stroke="var(--blue)" stroke-width="1.6" stroke-linecap="round" d="M14 6.5a4 4 0 0 1 3.5 3.5M14 2.8a7.6 7.6 0 0 1 7.2 7.2"/>
  </svg>
  <div class="icon-slot" role="img" aria-label="Icon of a consultation across a desk" style="left:470px;top:509px;width:60px;height:52px;"></div>
</section>
<div class="label" style="left:755px;top:664px;">3 WINDOWS</div>

<!-- FRONT 6 WINDOWS -->
<section class="panel front" aria-label="Front six window signage">
  <svg class="shape" viewBox="0 0 1017 410" preserveAspectRatio="none" aria-hidden="true">
    <path d="M0 150 C 50 50, 170 0, 300 0 L 820 0 C 935 30, 930 220, 905 410 L 0 410 Z" fill="var(--blue)"/>
    <path d="M0 172 C 70 60, 210 4, 430 4 L 800 4 C 905 20, 905 220, 885 410 L 0 410 Z" fill="var(--white)"/>
  </svg>
  <div class="c brand-mark" style="left:421px;top:60px;width:66px;height:66px;"></div>
  <div class="c brand-name" style="left:421px;top:148px;font-size:21px;letter-spacing:1px;">
    <span>VARDEN AND PELLOSI</span><span>DENTAL &amp; ORTHODONTICS</span>
  </div>

  <div class="c doc-name" style="left:86px;top:222px;font-size:29px;">DR. VARDEN</div>
  <div class="c phone" style="left:86px;top:256px;font-size:29px;">415.555.0187</div>
  <div class="c doc-role" style="left:254px;top:238px;font-size:17px;line-height:1.25;">General Dentistry<br>&amp;<br>Orthodontics</div>

  <div class="c doc-name" style="left:422px;top:222px;font-size:29px;">DR. PELLOSI</div>
  <div class="c phone" style="left:422px;top:256px;font-size:29px;">415.555.0243</div>
  <div class="c doc-role" style="left:591px;top:238px;font-size:17px;line-height:1.25;">Oral Surgery &amp;<br>Sedationeral<br>Dentistry</div>

  <div class="c doc-name" style="left:765px;top:222px;font-size:23px;">1938 BIRCHWOOD AVE</div>
  <div class="c doc-role" style="left:765px;top:254px;font-size:17px;">Address</div>

  <div class="banner" style="top:284px;width:853px;height:31px;">
    <div class="banner-item" style="left:85px;font-size:12px;">CLEARMOLD</div>
    <div class="banner-item" style="left:254px;font-size:12px;">BRACES</div>
    <div class="banner-item" style="left:423px;font-size:12px;">IMPLANTS</div>
    <div class="banner-item" style="left:594px;font-size:12px;">WHITING</div>
    <div class="banner-item" style="left:765px;font-size:12px;">ORAL SURGERY</div>
  </div>

  <div class="icon-slot" role="img" aria-label="Icon of a clear aligner tray" style="left:86px;top:364px;width:74px;height:28px;"></div>
  <div class="icon-slot" role="img" aria-label="Icon of teeth with braces" style="left:254px;top:364px;width:50px;height:34px;"></div>
  <div class="icon-slot" role="img" aria-label="Icon of a dental implant" style="left:423px;top:364px;width:26px;height:38px;"></div>
  <div class="icon-slot" role="img" aria-label="Icon of a sparkling white tooth" style="left:594px;top:364px;width:34px;height:38px;"></div>
  <div class="icon-slot" role="img" aria-label="Icon of a tooth with dental tools" style="left:765px;top:364px;width:48px;height:40px;"></div>
</section>
<div class="label" style="left:531px;top:1145px;">6 WINDOWS</div>

</body>
</html>
```